Kestrel Facilities Business Card Design

We would now like to design business cards with the new Kestrel Facilities logo

Target Market(s)

Professional

Industry/Entity Type

Professional services

Contact Information for Business Card

Employee name, title, phone number, email address, corporate office address and logo.

Font styles to use
Sans Serif

Colors
0054AA
0677BA
7BADD7
CADEEF
E8F1F8

Requirements
Must have
• My logo
Should not have
• any other pictures or images besides my logo

```html
<!DOCTYPE html>
<html lang="en">
<head>
<meta charset="utf-8">
<title>Kestrel Facilities Business Card</title>
<link rel="stylesheet" href="https://fonts.googleapis.com/css2?family=Montserrat:wght@400;500;600&display=swap">
<style>
  :root {
    --backdrop: #1c1c1d;
    --card: #2a2a2b;
    --card-back-top: #2c2c2d;
    --card-back-bottom: #1f1f20;
    --brand-blue: #3a82cf;
    --text-light: #f1f1f1;
  }
  * { margin: 0; padding: 0; box-sizing: border-box; }
  html, body {
    width: 1200px; height: 900px; overflow: hidden;
    background: var(--backdrop);
    font-family: "Montserrat", sans-serif;
  }
  .canvas {
    position: relative; width: 1200px; height: 900px;
  }
  .card {
    position: absolute; left: 267px;
    width: 666px; height: 380px;
    overflow: hidden;
    box-shadow: 0 18px 40px rgba(0,0,0,0.55);
  }
  .card-back { top: 45px; }
  .card-front { top: 475px; background: var(--card); }
  .bottom-band {
    position: absolute; left: 0; right: 0; bottom: 0;
    height: 8px; background: var(--brand-blue);
  }
  .pattern-field {
    position: absolute; inset: 0 0 8px 0;
    background: linear-gradient(160deg, var(--card-back-top), var(--card-back-bottom));
  }
  .back-mark {
    position: absolute; right: 40px; bottom: 44px;
    color: var(--brand-blue); font-weight: 600; font-size: 18px;
    letter-spacing: 0.5px;
  }
  .brand {
    position: absolute; left: 60px; top: 128px; width: 250px;
    color: var(--brand-blue); font-weight: 600;
    font-size: 44px; line-height: 1.05; letter-spacing: 1px;
    text-transform: uppercase;
  }
  .divider {
    position: absolute; left: 336px; top: 110px;
    width: 2px; height: 160px; background: var(--brand-blue);
  }
  .contact {
    position: absolute; left: 366px; top: 112px;
    color: var(--text-light);
  }
  .person-name {
    color: var(--brand-blue); font-weight: 600;
    font-size: 24px; letter-spacing: 1.5px; text-transform: uppercase;
  }
  .person-title { font-size: 17px; margin-top: 2px; }
  .address { font-size: 17px; line-height: 1.3; margin-top: 18px; }
  .lines { margin-top: 14px; font-size: 18px; line-height: 1.5; }
  .line { display: flex; align-items: center; gap: 10px; }
  .line svg { width: 15px; height: 15px; flex: none; }
</style>
</head>
<body>
<div class="canvas">
  <section class="card card-back">
    <div class="pattern-field" role="img" aria-label="Dark embossed repeating brand monogram pattern"></div>
    <div class="back-mark">Kestrel Facilities</div>
    <div class="bottom-band"></div>
  </section>

  <section class="card card-front">
    <div class="brand">Kestrel Facilities</div>
    <div class="divider"></div>
    <div class="contact">
      <div class="person-name">Martin Calloway</div>
      <div class="person-title">Director</div>
      <div class="address">1187 Birchwood Lane<br>Fernhill, OR 97408</div>
      <div class="lines">
        <div class="line">
          <svg viewBox="0 0 16 16" fill="none" stroke="#3a82cf" stroke-width="1.6" stroke-linecap="round" stroke-linejoin="round"><path d="M4 1.5l2.5 3-1.5 1.8c.8 1.8 2.4 3.4 4.2 4.2L11 9l3 2.5-1.5 2.5C7 13.5 2.5 9 2 3.5z"/></svg>
          <span>(555) 318-2046</span>
        </div>
        <div class="line">
          <svg viewBox="0 0 16 16" fill="none" stroke="#3a82cf" stroke-width="1.6" stroke-linejoin="round"><rect x="1.5" y="3.5" width="13" height="9"/><path d="M1.5 3.5L8 9l6.5-5.5"/></svg>
          <span>info@kestrelfacilities.com</span>
        </div>
      </div>
    </div>
    <div class="bottom-band"></div>
  </section>
</div>
</body>
</html>
```